Re-design and craft the perfect CV platform

We are building a CV-based platform designed to connect employees and employers, with a strong focus on individual users. As we're just starting out, we're looking to have our platform and logo redesigned to better reflect our vision
https://app.zelvorhire.com/
Colors like in the logo attached
#87C032 #6A6E71 #618930 - also you can add more colors if you like.
https://app.zelvorhire.com/dashboard - This page would be nice if you plan it, like personal Bio dashboard. Attached picture (Dashboard wanted) one idea from how we would like to be, but we are open for new professional ideas/solutions.
https://app.zelvorhire.com/posts - On this page we want to be showed the jobs posted. Attached one picture about our idea (jobs page wanted)
https://app.zelvorhire.com/profile - design something nice.
Only Photoshop, Illustrator or Figma
Other pictures from the app attached (as looking right now)

Target Market(s)

Job seekers, HR, Recruiters

Industry/Entity Type

HR Tech

Number of Pages Required

5+ page

Colors
00AB8E
00BBA5
67D7C9
C6EFE9
E9F9F6

```html
<!DOCTYPE html>
<html lang="en">
<head>
<meta charset="UTF-8">
<title>Zelvor – Login</title>
<link rel="stylesheet" href="https://fonts.googleapis.com/css2?family=Poppins:wght@400;500;600;700&display=swap">
<style>
  :root {
    --brand-green: #87C032;
    --brand-green-dark: #618930;
    --panel-grey: #5a5d62;
    --text-grey: #63676b;
    --field-bg: #f4f4f4;
    --ring: #d9d9d9;
    --white: #ffffff;
  }
  * { box-sizing: border-box; margin: 0; padding: 0; }
  html, body { width: 1200px; height: 712px; overflow: hidden; background: var(--white); }
  body { font-family: "Poppins", sans-serif; color: var(--text-grey); position: relative; }

  .brand-panel {
    position: absolute; left: 0; top: 0; width: 480px; height: 712px;
    background: var(--panel-grey);
    border-radius: 0 36px 30px 0;
    color: var(--white); text-align: center;
  }
  .brand-panel__name {
    position: absolute; top: 262px; left: 0; width: 100%;
    font-size: 56px; font-weight: 600; letter-spacing: 2px; line-height: 1;
    color: var(--white);
  }
  .brand-panel__title {
    position: absolute; top: 361px; left: 0; width: 100%;
    font-size: 19px; font-weight: 700;
  }
  .brand-panel__lead {
    position: absolute; top: 388px; left: 0; width: 100%;
    font-size: 15.5px; font-weight: 600;
  }
  .brand-panel__terms {
    position: absolute; top: 414px; left: 60px; width: 360px;
    font-size: 15.5px; line-height: 24px; font-weight: 400;
  }
  .brand-panel__terms a {
    color: var(--brand-green); font-weight: 500; text-decoration: none;
    border-bottom: 1px solid var(--brand-green);
  }

  .btn-create {
    position: absolute; left: 1008px; top: 20px; width: 158px; height: 35px;
    border-radius: 18px; background: var(--brand-green); color: var(--white);
    font-size: 12.5px; font-weight: 700; display: flex; align-items: center; justify-content: center;
  }

  .login { position: absolute; left: 543px; top: 0; width: 420px; }
  .login__title {
    position: absolute; top: 193px; left: -2px; white-space: nowrap;
    font-size: 36px; font-weight: 700; color: var(--text-grey); letter-spacing: 0.3px;
  }
  .login__subtitle { position: absolute; top: 237px; font-size: 15.5px; white-space: nowrap; }
  .field-label {
    position: absolute; font-size: 16px; font-weight: 500; letter-spacing: 0.2px; white-space: nowrap;
  }
  .field-input {
    position: absolute; width: 417px; height: 47px; background: var(--field-bg);
    border-radius: 6px; border: none;
  }
  .forgot-link {
    position: absolute; top: 373px; right: 3px; font-size: 13.5px; color: var(--text-grey);
    text-decoration: none; border-bottom: 1px solid var(--text-grey); line-height: 18px;
  }
  .remember { position: absolute; top: 463px; display: flex; align-items: center; gap: 15px; }
  .remember__box {
    width: 20px; height: 20px; background: #ededed; border-radius: 3px;
    display: flex; align-items: center; justify-content: center;
  }
  .remember__label { font-size: 15px; font-weight: 500; }
  .btn-signin {
    position: absolute; top: 492px; left: 0; width: 186px; height: 47px; border-radius: 24px;
    background: var(--brand-green); color: var(--white); font-size: 17px; font-weight: 700;
    display: flex; align-items: center; justify-content: center; gap: 6px;
  }
  .signup-link {
    position: absolute; top: 506px; left: 204px; font-size: 12.5px; font-weight: 700;
    color: var(--text-grey); text-decoration: none; border-bottom: 1px solid var(--text-grey);
    line-height: 17px; white-space: nowrap;
  }

  .rings { position: absolute; left: 0; top: 0; }
  .badge {
    position: absolute; left: 1088px; top: 604px; width: 78px; height: 78px; border-radius: 50%;
    background: var(--white); box-shadow: 0 2px 10px rgba(0,0,0,0.12);
    display: flex; align-items: center; justify-content: center;
    font-size: 13px; font-weight: 600; color: var(--brand-green);
  }
</style>
</head>
<body>
  <svg class="rings" width="1200" height="712" aria-hidden="true">
    <g fill="none" stroke="var(--ring)" stroke-width="1.2">
      <circle cx="1088" cy="698" r="205"/>
      <circle cx="1088" cy="698" r="155"/>
      <circle cx="1088" cy="698" r="105"/>
      <circle cx="1088" cy="698" r="55"/>
    </g>
  </svg>

  <aside class="brand-panel">
    <div class="brand-panel__name">ZELVOR</div>
    <h2 class="brand-panel__title">RECRUITMENT WEB APP ACCESS</h2>
    <p class="brand-panel__lead">Create an account or sing in.</p>
    <p class="brand-panel__terms">By creating an account or signing in, you understand and agree to Zelvor Terms. You also acknowledge <a href="#">Our Cookie</a> and <a href="#">Privacy policies.</a></p>
  </aside>

  <a class="btn-create">CREATE ACCOUNT</a>

  <main class="login">
    <h1 class="login__title">LOGIN INTO ZELVOR</h1>
    <p class="login__subtitle">enter your login details below.</p>

    <label class="field-label" style="top:282px">ENTER YOUR EMAIL ADDRES</label>
    <div class="field-input" style="top:309px"></div>

    <label class="field-label" style="top:371px">PASSWORD</label>
    <a class="forgot-link" href="#">Forget your Pasword!</a>
    <div class="field-input" style="top:398px"></div>

    <div class="remember">
      <span class="remember__box">
        <svg width="11" height="11" viewBox="0 0 12 12"><path d="M7 1l4 4-2 1-2 2 0 2-1 1-2.2-2.2L1 12l-.5-.5 3.2-2.8L1.5 6.5l1-1 2 0 2-2z" fill="#6A6E71"/></svg>
      </span>
      <span class="remember__label">REMEMBER ME</span>
    </div>

    <a class="btn-signin">SIGN IN
      <svg width="20" height="20" viewBox="0 0 20 20" aria-hidden="true">
        <path d="M10 2h7v16h-7" fill="none" stroke="#fff" stroke-width="2"/>
        <path d="M2 10h9M8 6.5l3.5 3.5L8 13.5" fill="none" stroke="#fff" stroke-width="2"/>
      </svg>
    </a>
    <a class="signup-link" href="#">DONT HAVE AN ACCOUNT?</a>
  </main>

  <div class="badge">ZELVOR</div>
</body>
</html>
```